Make a medical leaflet for my patients undergoing ankle blocks

I have a very boring text only leaflet I would like to turn into a professional appealing medical leaflet to give to my patients. I would like to get this onto two pages of a4 if possible and its intended for electronic distribution mainly.
This will be for patients so it must be professional.
It must also contain a copyright logo on it and my name near the start (Dr Paul Venning) so my colleagues can't use it easily.
Target Market(s)
Patients undergoing surgery
Industry/Entity Type
Medical
Font styles to use
Other font styles liked:
- no idea, you tell me
Requirements
Must have
- the information contained on the attachment
- look professional
- a copyright on it
Nice to have
- the harbour infirmary logo
Should not have
- Any spelling, grammatical or linguistic errors
- Any font less than size 12

```html
<!DOCTYPE html>
<html lang="en">
<head>
<meta charset="utf-8">
<title>Undergoing Ankle Blocks – Patient Leaflet</title>
<link rel="stylesheet" href="https://fonts.googleapis.com/css2?family=Montserrat:wght@500;600;700;800&family=Open+Sans:wght@400;600&display=swap">
<style>
  :root{
    --brand:#1f62a8;
    --brand-dark:#184f8a;
    --ink:#3d3d3d;
    --muted:#666;
    --paper:#ffffff;
    --backdrop:#e9eaec;
    --rule:#b9c3cf;
    --photo-a:#dfe9f1;
    --photo-b:#c9d8e6;
    --skin-a:#ecd9cc;
    --skin-b:#d9b9a3;
  }
  *{box-sizing:border-box;margin:0;padding:0}
  html,body{width:1200px;height:888px;overflow:hidden}
  body{background:var(--backdrop);font-family:"Open Sans",Arial,sans-serif;color:var(--ink);position:relative}
  .page{position:absolute;top:66px;width:498px;height:704px;background:var(--paper);box-shadow:0 6px 14px rgba(0,0,0,.18)}
  .page--front{left:74px}
  .page--back{left:628px}
  .page::after{content:"";position:absolute;left:0;right:0;bottom:0;height:5px;background:var(--brand)}
  .abs{position:absolute}
  .body-text{font-size:7.7px;line-height:1.42;color:var(--ink)}
  .body-text p{margin-bottom:4px;text-align:justify}

  .hospital-name{font-family:"Open Sans",Arial,sans-serif;font-weight:400;color:var(--brand-dark);font-size:19px;letter-spacing:-.2px}
  .group-line{font-size:8px;color:var(--muted)}

  .infirmary-tile{left:364px;top:0;width:118px;height:109px;background:var(--brand);display:flex;align-items:center;justify-content:center;padding:0 10px}
  .infirmary-tile .name{font-family:"Open Sans",Arial,sans-serif;font-weight:600;font-size:11px;line-height:1.35;color:#fff;text-align:center}

  .name-band{left:0;top:85px;width:262px;height:22px}
  .name-band span{position:absolute;left:55px;top:4px;font-family:Montserrat,Arial,sans-serif;font-weight:600;color:#fff;font-size:12.5px}

  .photo{background:linear-gradient(135deg,var(--photo-a),var(--photo-b))}
  .photo--foot{background:radial-gradient(ellipse at 55% 50%,var(--skin-a),var(--skin-b) 70%,#f3eeea)}

  .title{font-family:Montserrat,Arial,sans-serif;font-weight:800;color:var(--brand);font-size:16.5px}

  .pill{position:absolute;transform:translateX(-50%);background:var(--brand);color:#fff;font-family:Montserrat,Arial,sans-serif;font-weight:700;font-size:9.6px;padding:4px 11px;border-radius:11px;white-space:nowrap;letter-spacing:.2px}
  .rule{position:absolute;height:1px;background:var(--brand)}

  .outline-box{border:1.2px solid var(--brand);border-radius:11px}
  .benefits{list-style:none;text-align:center;font-size:7.4px;line-height:1.95;padding-top:14px}
  .benefits svg{width:8px;height:8px;vertical-align:-1px;margin-right:5px}

  .risk-table{border-collapse:collapse;width:464px;font-size:7.4px;line-height:1.32}
  .risk-table td{border:1px solid var(--rule);vertical-align:top;padding:6px 8px 5px 8px}
  .risk-table td:first-child{width:152px;color:var(--brand);font-family:Montserrat,Arial,sans-serif;font-weight:700;font-size:8px}
  .risk-table tr:first-child td{height:64px}
  .risk-table tr:nth-child(2) td{height:41px}

  .subhead{font-family:Montserrat,Arial,sans-serif;font-weight:600;color:var(--brand);font-size:8.8px;text-align:center;width:100%}
  .centered{text-align:center}
  .body-text.centered{text-align:center}
  .closing{font-family:Montserrat,Arial,sans-serif;font-weight:600;color:var(--brand);font-size:9.8px;line-height:1.35;text-align:center}
  .doctor-name{font-family:Montserrat,Arial,sans-serif;font-weight:700;color:var(--brand);font-size:16px}
  .divider-v{width:1px;background:var(--rule)}
  .copyright{font-size:6.5px;color:var(--muted)}
</style>
</head>
<body>

<section class="page page--front">
  <div class="abs hospital-name" style="left:18px;top:12px">Riverside Bridge Hospital</div>
  <div class="abs group-line" style="left:39px;top:51px">part of <span style="font-size:13px;color:var(--brand-dark)">Meridian Health Group</span></div>

  <div class="abs infirmary-tile">
    <span class="name">The Harbour Infirmary</span>
  </div>

  <div class="abs name-band">
    <svg width="262" height="22" viewBox="0 0 262 22"><polygon points="0,0 250,0 262,22 0,22" fill="#1f62a8"/></svg>
    <span>DR PAUL VENNING</span>
  </div>

  <div class="abs photo" role="img" aria-label="Photo of a smiling patient giving a thumbs up" style="left:0;top:109px;width:222px;height:200px"></div>

  <h1 class="abs title" style="left:227px;top:121px">UNDERGOING ANKLE BLOCKS</h1>

  <div class="abs body-text" style="left:227px;top:148px;width:256px">
    <p>You are scheduled to have surgery on your foot. It is my normal practice to offer and perform (with your consent) an ankle block. This is an optional injection of numbing liquid to the nerves which supply your foot. The ankle block can be performed when you are awake, sedated or under general anaesthesia.</p>
    <p>The ankle block can be combined with a general anaesthetic and with sedation. It can also be used to allow surgery to be performed with you wide awake in certain cases.</p>
    <p>Having or not having an ankle block does not change the pre operative fasting guidelines you have been given.</p>
    <p>There is a fee for performing an ankle block. Please consult my initial introductory email and terms of business for details.</p>
  </div>

  <div class="abs outline-box" style="left:29px;top:332px;width:439px;height:97px">
    <ul class="benefits">
      <li><svg viewBox="0 0 10 10"><circle cx="5" cy="5" r="4.2" fill="none" stroke="#1f62a8" stroke-width="1"/><path d="M3 5.2l1.5 1.5L8.5 2" fill="none" stroke="#1f62a8" stroke-width="1.3"/></svg>Excellent pain relief - usually 10 - 14 hours (and rarely 24 - 48 hours)</li>
      <li><svg viewBox="0 0 10 10"><circle cx="5" cy="5" r="4.2" fill="none" stroke="#1f62a8" stroke-width="1"/><path d="M3 5.2l1.5 1.5L8.5 2" fill="none" stroke="#1f62a8" stroke-width="1.3"/></svg>Avoiding traditional painkillers, resulting in less post operative nausea and vomiting</li>
      <li><svg viewBox="0 0 10 10"><circle cx="5" cy="5" r="4.2" fill="none" stroke="#1f62a8" stroke-width="1"/><path d="M3 5.2l1.5 1.5L8.5 2" fill="none" stroke="#1f62a8" stroke-width="1.3"/></svg>The option to avoid a general anaesthetic (if you wish)</li>
      <li><svg viewBox="0 0 10 10"><circle cx="5" cy="5" r="4.2" fill="none" stroke="#1f62a8" stroke-width="1"/><path d="M3 5.2l1.5 1.5L8.5 2" fill="none" stroke="#1f62a8" stroke-width="1.3"/></svg>A faster recovery from the general anaesthetic</li>
      <li><svg viewBox="0 0 10 10"><circle cx="5" cy="5" r="4.2" fill="none" stroke="#1f62a8" stroke-width="1"/><path d="M3 5.2l1.5 1.5L8.5 2" fill="none" stroke="#1f62a8" stroke-width="1.3"/></svg>Certain surgery requires an overnight stay in hospital without an ankle block</li>
    </ul>
  </div>
  <div class="pill" style="left:249px;top:321px">WHAT ARE THE BENEFITS</div>

  <div class="rule" style="left:132px;width:235px;top:454px"></div>
  <div class="pill" style="left:249px;top:445px">WHAT ARE THE RISKS?</div>

  <p class="abs body-text centered" style="left:0;width:498px;top:475px">As with all injections, there is the risk of bruising, bleeding and infection.</p>

  <table class="abs risk-table" style="left:18px;top:492px">
    <tr>
      <td>NERVE DAMAGE</td>
      <td>Occurs 1 in 5000 nerve blocks.<br>Creates an area of numbness or weakness/paralysis in some / all the foot.<br>Majority of nerve injuries will heal themselves within a year.<br>There is no treatment to fix it.<br>If the block has not worn off after 72 hours please let me know.</td>
    </tr>
    <tr>
      <td>FAILURE</td>
      <td>The success rate with ankle blocks is 98 - 99%.<br>Some blocks will fail, partially or totally.<br>If total failure, I will discuss repeating the block with your consent.</td>
    </tr>
    <tr>
      <td>PAIN DURING OPERATION</td>
      <td>If you choose to have wide awake surgery or surgery under sedation<br>the surgery will stop and I will discuss three options with you:<br>- &nbsp;more numbing liquid to be injected by the surgeon<br>- &nbsp;more sedation / painkiller<br>- &nbsp;having a general anaesthetic</td>
    </tr>
  </table>

  <p class="abs body-text centered" style="left:26px;width:446px;top:666px">If you decide to undergo surgery awake or sedated, there is a risk you will need to have a general anaesthetic if you feel pain. This is why the starvation instructions of awake surgery and general anaesthesia are the same.</p>
</section>

<section class="page page--back">
  <div class="rule" style="left:131px;width:234px;top:27px"></div>
  <div class="pill" style="left:248px;top:18px">HOW IS IT DONE</div>

  <h2 class="abs subhead" style="top:57px">IF YOU CHOOSE AWAKE SURGERY OR SURGERY WITH SEDATION -</h2>
  <p class="abs body-text centered" style="left:22px;width:454px;top:74px">Numbing liquid is injected around the nerves which supply your foot. The ankle block takes 5 - 10 minutes to perform and requires 4 - 5 injections. Approximately 10 - 20 minutes to make your foot numb to pain. I will check the ankle block is working before we start surgery using cold spray. Sensations of touch, pressure, vibration and movement will still be felt. I will use a screen so you can't see the surgery (unless you would like to see). Some patients bring headphones to block out the noise of the operation.</p>

  <h2 class="abs subhead" style="top:151px">IF YOU CHOOSE A GENERAL ANAESTHETIC</h2>
  <p class="abs body-text centered" style="left:22px;width:454px;top:169px">I will perform the ankle block after I start the general anaesthetic. You should wake up from your surgery with a comfortable and numb foot/feet. If you wake in pain, we can repeat the ankle block or provide traditional painkillers.</p>
  <p class="abs body-text centered" style="left:12px;width:476px;top:205px">Whatever you choose, there will be a cannula placed in your hand and heart and oxygen monitoring throughout.</p>

  <div class="rule" style="left:300px;width:178px;top:236px"></div>
  <div class="pill" style="left:259px;top:227px">AFTER SURGERY</div>

  <div class="abs photo photo--foot" role="img" aria-label="Photo of a bandaged foot and ankle" style="left:0;top:242px;width:196px;height:220px"></div>

  <div class="abs body-text" style="left:198px;top:256px;width:280px">
    <p>You will go to the recovery area and then onto the ward when you are ready. It will be difficult to walk while the block is working, so physiotherapists will help you first walk. If you need crutches they will teach you how to use them.</p>
    <p>Your foot will be numb and so you will not feel where your foot is in relation to nearby objects. As a result, it is easy to knock your foot. Please take extra care while your foot is still numb.</p>
    <p>As the block wears off, the foot may feel slightly painful, tingly or hot. At this point you should take your painkillers I have prescribed. Depending on your medical history you will have up to three painkillers. I would suggest to start with all three. You will also have an anti - sickness prescribed if one of the painkillers (typically codeine or morphine) makes you feel sick.</p>
    <p>Occasionally (1 - 2%), pain when the block wears off will be severe. In this case contact your surgeon's secretary. We can use stronger pain medication, but there will be a charge in writing and getting the private prescription to you (please see my terms of business) via courier.</p>
  </div>

  <div class="abs outline-box" style="left:30px;top:477px;width:434px;height:65px"></div>
  <div class="pill" style="left:248px;top:467px">THE ALTERNATIVE</div>
  <p class="abs body-text centered" style="left:30px;width:434px;top:495px">If you do not have an ankle block your surgery can still proceed.<br>Post operative pain can be managed with traditional painkillers.<br>However, you are more likely to need an overnight stay or feel sick after the anaesthetic.</p>

  <p class="abs closing" style="left:40px;width:418px;top:559px">If you have any further questions about an ankle block I will see you the day of your surgery. Alternatively, you can request the following optional services (as mentioned in my terms of business).</p>

  <div class="abs hospital-name" style="left:16px;top:640px;font-size:17px">Riverside Bridge Hospital</div>
  <div class="abs group-line" style="left:33px;top:674px;font-size:7px">part of <span style="font-size:11px;color:var(--brand-dark)">Meridian Health Group</span></div>
  <div class="abs divider-v" style="left:258px;top:638px;height:46px"></div>
  <div class="abs doctor-name" style="right:18px;top:649px">DR PAUL VENNING</div>
  <p class="abs copyright" style="right:18px;top:678px">© Dr Paul Venning. All rights reserved.</p>
</section>

</body>
</html>
```